Anesthesia Medical Practice Business Card

We need a business card to hand out to surgeons with my basic information. Something that stands out but is not over the top. The medical community is rather conservative. I'd like them to call me first when flipping through their rolodex of anesthesiologists. I'd like the card to communicate confidence, control, professionalism yet serenity. I don't want the card to be pricey to print.

he logo will be provided as a vector graphic in addition to a complete business card design including the logo

Lem Varo Keshtel, M.D.
Board Certified Anesthesiologist

(555) 386-2157

lkeshtel@quorvanmail.example

Mailing Address:
47315 Brindlecove Ave.
Suite 382-6475
Los Angeles, CA 90877

A logo that inegrates my initials perhaps
LK MD
My initials are LK and MD as in Medical Doctor

or
perhaps a physician in surgical mask and cap caring for a patient

Target Market(s)

Surgeons who need anesthesia services

Industry/Entity Type

Medical

Requirements
Must have
• the logo will be provided as a vector graphic in addition to a complete business card design including the logo

Lem Varo Keshtel, M.D.

(555) 386-2157

lkeshtel@quorvanmail.example

Mailing Address:
47315 Brindlecove Ave.
Suite 382-6475
Los Angeles, CA 90877

Nice to have
• A logo that inegrates my initials perhaps
LK MD

or

```html
<!DOCTYPE html>
<html lang="en">
<head>
<meta charset="utf-8">
<title>Lem Varo Keshtel, M.D. — Business Card</title>
<link rel="stylesheet" href="https://fonts.googleapis.com/css2?family=Josefin+Sans:wght@300;400;600&display=swap">
<style>
  :root {
    --backdrop: #463a33;
    --card-black: #0d0d0e;
    --card-sheen: #222325;
    --ink-white: #f2f2f2;
    --ink-grey: #b5b5b5;
  }
  * { box-sizing: border-box; margin: 0; padding: 0; }
  html, body {
    width: 1200px;
    height: 1000px;
    overflow: hidden;
    background: var(--backdrop);
  }
  .stage {
    width: 1200px;
    height: 1000px;
    display: flex;
    align-items: center;
    justify-content: center;
  }
  .business-card {
    width: 840px;
    height: 480px;
    background: radial-gradient(ellipse at 55% 35%, var(--card-sheen) 0%, var(--card-black) 70%);
    border-radius: 4px;
    display: flex;
    flex-direction: column;
    align-items: center;
    padding-top: 92px;
    font-family: "Josefin Sans", sans-serif;
    text-align: center;
    color: var(--ink-grey);
  }
  .practice-mark {
    display: flex;
    align-items: center;
    gap: 14px;
    height: 60px;
    margin-bottom: 48px;
  }
  .practice-mark__dot {
    width: 26px;
    height: 26px;
    border-radius: 50%;
    background: var(--ink-white);
    flex: none;
  }
  .practice-mark__name {
    font-weight: 300;
    font-size: 30px;
    letter-spacing: 2px;
    color: var(--ink-white);
    padding-top: 5px;
  }
  .doctor-name {
    font-weight: 600;
    font-size: 27px;
    letter-spacing: 1px;
    color: var(--ink-white);
  }
  .doctor-title {
    font-weight: 400;
    font-size: 15px;
    letter-spacing: 0.5px;
    color: var(--ink-grey);
    margin-top: 4px;
  }
  .contact {
    margin-top: 18px;
    font-weight: 300;
    font-size: 16px;
    line-height: 1.4;
  }
  .address {
    margin-top: 12px;
    font-weight: 300;
    font-size: 16px;
    line-height: 1.4;
    font-style: normal;
  }
</style>
</head>
<body>
  <main class="stage">
    <section class="business-card">
      <div class="practice-mark">
        <span class="practice-mark__dot"></span>
        <span class="practice-mark__name">Keshtel Anesthesia</span>
      </div>
      <h1 class="doctor-name">Lem Varo Keshtel, M.D.</h1>
      <p class="doctor-title">Board Certified Anesthesiologist</p>
      <div class="contact">
        <p class="contact__phone">(555) 386-2157</p>
        <p class="contact__email">lkeshtel@quorvanmail.example</p>
      </div>
      <address class="address">
        Mailing Address:<br>
        47315 Brindlecove Ave.<br>
        Suite 382-6475<br>
        Los Angeles, CA 90877
      </address>
    </section>
  </main>
</body>
</html>
```